Website for Dental Office - The Bright Arch Clinic

The bright arch clinic is a dental office offering cosmetic dentistry, general dentistry, and multi-specialty dental care all under one roof in our state-of-the-art cosmetic dental center. We are particularly striving to provide services that fit the need of the young generation. Thus, we hope to have a modern, professional concise website that represents our spirit.

*Should be able to switch from English to Chinese

6 sections besides homepage:
Home, Meet us, Services,
Patient Info, Cases&Reviews, Blog, Contact

The Services sections should contain multiple subsections such as cleaning and prevention, cosmetic dentistry, implant dentistry, removable dentures, etc...
The Patient Info section is also intended to contain several subsections such as
New Patient offer, accepted Insurance, patient portal, helpful tips, etc...

Target Market(s)

young generation

Coding

Coded - Design and coding required

Number of Pages Required

5+ page

Font styles to use
Sans Serif

Colors
0592cd
33a6d7
85cae6
00a990
33b8a4
86cfc6
cee9f5
cfeae6
3277b5

Requirements
Must have
• *Should be able to switch from English to Chinese
Nice to have
• http://www.thebrightarchclinic.com/
• As a reference, the above link is the current website, but we would like to change the appearance and the content (our new logo's picture is attached)

```html
<!DOCTYPE html>
<html lang="en">
<head>
<meta charset="utf-8">
<title>The Bright Arch Clinic</title>
<link href="https://fonts.googleapis.com/css2?family=Montserrat:wght@400;500;600;700&family=Open+Sans:wght@400;600&display=swap" rel="stylesheet">
<style>
:root{
  --blue:#0592cd; --blue2:#33a6d7; --blue3:#85cae6; --blue-pale:#cee9f5;
  --teal:#00a990; --teal2:#33b8a4; --teal3:#86cfc6; --teal-pale:#cfeae6;
  --navy:#3277b5; --ink:#2b2f36; --grey:#8a9097; --line:#e3e8ec; --white:#fff;
}
*{box-sizing:border-box;margin:0;padding:0}
html,body{width:1200px;height:4508px;overflow:hidden}
body{font-family:"Open Sans",Arial,sans-serif;color:var(--ink);background:var(--white);position:relative}
h1,h2,h3,h4,.btn,.nav a{font-family:"Montserrat",Arial,sans-serif}
.abs{position:absolute}
.btn{display:inline-block;background:var(--teal);color:#fff;font-size:13px;font-weight:600;letter-spacing:.5px;padding:15px 30px;border-radius:3px;text-transform:uppercase}
.small{font-size:12px;line-height:1.7;color:var(--grey)}
.ph{display:block}
.sec-title{font-size:40px;font-weight:600;text-align:center;color:var(--ink)}
.sec-title span{color:var(--blue)}

/* header */
.topbar{left:0;top:0;width:1200px;height:170px}
.social{left:78px;top:10px;display:flex;gap:8px}
.social i{width:24px;height:24px;border-radius:50%;background:var(--blue);display:block}
.toplinks{right:40px;top:12px;display:flex;gap:26px;font-size:14px;color:var(--blue)}
.logo{left:78px;top:58px;display:flex;align-items:center;gap:12px}
.logo b{width:40px;height:40px;background:var(--blue);border-radius:4px;display:block;flex:none}
.logo span{font-family:"Montserrat",sans-serif;font-weight:700;font-size:24px;color:var(--blue);line-height:1.05;width:200px}
.info{top:60px;display:flex;gap:14px}
.info .ic{width:46px;height:46px;border-radius:50%;background:var(--teal);display:flex;align-items:center;justify-content:center;flex:none}
.info h4{font-size:13px;font-weight:600;margin-bottom:3px}
.info p{font-size:12px;color:var(--grey);line-height:1.5}
.navbar{left:0;top:160px;width:1200px;height:60px;border-top:1px solid var(--line)}
.nav{position:absolute;left:78px;top:18px;display:flex;gap:34px}
.nav a{font-size:14px;font-weight:500;color:var(--ink);text-decoration:none;padding-bottom:6px}
.nav a.on{color:var(--teal);border-bottom:2px solid var(--teal)}
.navbar .search{position:absolute;left:780px;top:18px}
.navbar .btn{position:absolute;right:30px;top:4px;padding:15px 28px}

/* hero */
.hero{left:0;top:228px;width:1200px;height:640px;background:linear-gradient(90deg,#f4f7f8 0%,#e9eef0 35%,#b9c7cc 60%,#8ea2a9 100%)}
.hero-copy{left:78px;top:410px;width:540px}
.hero-copy h4{color:var(--teal);font-size:14px;font-weight:600;letter-spacing:.5px;margin-bottom:12px}
.hero-copy h1{color:var(--teal);font-size:58px;font-weight:600;line-height:1.05;margin-bottom:22px}
.hero-copy p{font-size:15px;line-height:1.6;color:#444;width:400px}
.cards{left:70px;top:810px;width:1060px;height:290px;background:#fff;display:flex;box-shadow:0 4px 16px rgba(0,0,0,.08)}
.card{flex:1;border-right:1px solid var(--line);padding:20px 22px;text-align:center}
.card:last-child{border-right:none}
.card .ph{height:110px;margin-bottom:22px;border-radius:3px}
.card h3{font-size:17px;font-weight:600;margin-bottom:10px}
.arrow{top:940px;color:var(--blue);font-size:34px;font-family:"Montserrat",sans-serif}

/* welcome */
.welcome{left:75px;top:1170px;width:530px}
.welcome h2{font-size:38px;font-weight:600;line-height:1.2;margin-bottom:24px}
.welcome h2 span{color:var(--blue)}
.welcome p{font-size:14px;line-height:1.75;color:var(--grey);margin-bottom:28px}
.welcome-img{left:650px;top:1165px;width:480px;height:345px;background:linear-gradient(135deg,#e7d3c8,#c99d8d 60%,#a07060)}

/* services */
.services{left:0;top:1640px;width:1200px;text-align:center}
.svc-row{display:flex;justify-content:center;gap:28px;margin-top:60px}
.svc{width:196px}
.svc svg{margin-bottom:16px}
.svc h3{font-size:17px;font-weight:600;margin-bottom:10px}
.services .btn{margin-top:40px}

/* reviews */
.reviews{left:0;top:2110px;width:1200px;height:600px;background:linear-gradient(180deg,#e9f5fb,#dcefe9)}
.reviews .sec-title{margin-top:70px}
.review{left:250px;top:2320px;width:700px;height:200px;background:#fff;border-radius:16px;box-shadow:0 6px 20px rgba(0,0,0,.08);text-align:center;padding:62px 70px 0}
.avatar{left:560px;top:2255px;width:80px;height:80px;border-radius:50%;background:linear-gradient(135deg,#cfe3ea,#8fb5c2);border:5px solid #fff}
.quote{font-family:"Montserrat",sans-serif;font-size:58px;font-weight:700;color:var(--teal);line-height:.7;margin-top:14px}
.dots{left:0;width:1200px;top:2660px;display:flex;justify-content:center;gap:8px}
.dots i{width:14px;height:14px;border-radius:50%;border:2px solid var(--blue3);display:block}
.dots i.on{background:var(--blue)}

/* blog */
.blog{left:0;top:2760px;width:1200px}
.post-text{width:260px}
.post-text .date{font-size:12px;color:var(--teal);text-align:right;margin-bottom:6px}
.post-text h3{font-size:22px;font-weight:600;line-height:1.2;margin-bottom:8px}
.post-text a{display:block;margin-top:12px;font-size:12px;font-weight:600;color:var(--teal);text-decoration:underline;font-family:"Montserrat",sans-serif}
.post-img{width:255px;height:170px}

/* team */
.team{left:0;top:3125px;width:1200px;height:380px;background:linear-gradient(100deg,#1d8fc9,#46b2dd 50%,#2d9ed4);text-align:center;color:#fff}
.team h2{font-size:40px;font-weight:500;margin-top:78px;margin-bottom:20px}
.team p{font-size:14px;line-height:1.6;width:460px;margin:0 auto 20px;color:#e6f4fb}
.team .btn{background:transparent;border:2px solid #fff;padding:11px 26px}

/* contact */
.contact{left:70px;top:3500px;width:470px}
.contact h2{font-size:40px;font-weight:600;margin:10px 0 30px}
.contact h2 span{color:var(--teal)}
.field{height:48px;border:1px solid var(--line);margin-bottom:14px;padding:14px;font-size:12px;color:var(--grey)}
.field.tall{height:120px}
.touch{left:600px;top:3460px;width:600px;height:540px;background:linear-gradient(160deg,var(--teal),#17b19a);color:#fff;padding:50px 60px}
.touch h2{font-size:40px;font-weight:600;margin-bottom:30px}
.touch li{list-style:none;display:flex;gap:16px;font-size:14px;margin-bottom:22px;line-height:1.5}
.touch li svg{flex:none}

/* footer */
.footer{left:0;top:4040px;width:1200px;height:468px;border-top:1px solid var(--line)}
.fcol{top:40px}
.fcol h4{font-size:17px;font-weight:600;margin-bottom:20px}
.fcol h4 span{color:var(--blue)}
.fcol li{list-style:none;font-size:13px;color:var(--grey);margin-bottom:9px}
.fsocial{display:flex;gap:8px;margin-top:20px}
.fsocial i{width:36px;height:36px;border-radius:3px;background:var(--blue);display:block}
.email-box{margin-top:18px;border:1px solid var(--line);height:40px;width:200px;padding:11px;font-size:12px;color:var(--grey)}
.copy{left:0;width:1200px;top:4470px;text-align:center;font-size:12px;color:var(--grey)}
</style>
</head>
<body>

<!-- Header -->
<div class="abs topbar">
  <div class="abs social"><i></i><i></i><i></i><i></i></div>
  <div class="abs toplinks"><span>Blog</span><span>Contact Us</span><span>EN ▾</span></div>
  <div class="abs logo"><b></b><span>THE BRIGHT ARCH CLINIC</span></div>
  <div class="abs info" style="left:640px">
    <div class="ic"><svg width="20" height="20" viewBox="0 0 24 24"><path d="M12 2a7 7 0 0 0-7 7c0 5 7 13 7 13s7-8 7-13a7 7 0 0 0-7-7zm0 9.5A2.5 2.5 0 1 1 12 6.5a2.5 2.5 0 0 1 0 5z" fill="#fff"/></svg></div>
    <div><h4>Location</h4><p>250 Harbor Lane, Suite 12,<br>Milton MA 02186</p></div>
  </div>
  <div class="abs info" style="left:960px">
    <div class="ic"><svg width="20" height="20" viewBox="0 0 24 24"><path d="M6.6 10.8a15 15 0 0 0 6.6 6.6l2.2-2.2c.3-.3.7-.4 1-.2 1.1.4 2.3.6 3.6.6.6 0 1 .4 1 1V20c0 .6-.4 1-1 1A17 17 0 0 1 3 4c0-.6.4-1 1-1h3.5c.6 0 1 .4 1 1 0 1.3.2 2.5.6 3.6.1.3 0 .7-.2 1z" fill="#fff"/></svg></div>
    <div><h4>Give us a Call</h4><p>617-555-0147</p></div>
  </div>
</div>
<div class="abs navbar">
  <nav class="nav"><a class="on">Home</a><a>About Us</a><a>Services</a><a>Patient Info</a><a>Cases &amp; Reviews</a><a>Blog</a><a>Contact</a></nav>
  <svg class="search" width="20" height="20" viewBox="0 0 24 24"><circle cx="10" cy="10" r="7" fill="none" stroke="#2b2f36" stroke-width="2"/><path d="M15 15l6 6" stroke="#2b2f36" stroke-width="2"/></svg>
  <span class="btn">Make an Appointment</span>
</div>

<!-- Hero -->
<div class="abs hero ph" role="img" aria-label="Dentist treating a patient in a modern dental chair with an x-ray screen"></div>
<div class="abs hero-copy">
  <h4>PROFESSIONAL DENTAL CARE</h4>
  <h1>Your smile.Our<br>passion.</h1>
  <p>We offer cosmetic dentistry, general dentistry and multi-specialty dental care all under one roof in our state-of-the-art cosmetic dental center.</p>
</div>
<div class="abs arrow" style="left:30px">‹</div>
<div class="abs arrow" style="left:1155px">›</div>
<div class="abs cards">
  <div class="card"><div class="ph" role="img" aria-label="Dental model of teeth" style="background:linear-gradient(135deg,#f6dede,#e7a9a9)"></div><h3>New Patient offer</h3><p class="small">Friendly first visit with a full check, cleaning and a clear care plan.</p></div>
  <div class="card"><div class="ph" role="img" aria-label="Stethoscope on a white desk" style="background:linear-gradient(135deg,#f1f3f6,#c9d3de)"></div><h3>Accepted Insurance</h3><p class="small">We work with most major plans so your care stays simple and fair.</p></div>
  <div class="card"><div class="ph" role="img" aria-label="Patient smiling at the clinic" style="background:linear-gradient(135deg,#eef3f5,#b6c8cf)"></div><h3>Patient Portal</h3><p class="small">Book visits, view records and message our team any time online.</p></div>
  <div class="card"><div class="ph" role="img" aria-label="Row of tooth models" style="background:linear-gradient(135deg,#f7f7f7,#d8dcdf)"></div><h3>Helpful Tips</h3><p class="small">Easy daily habits that keep your teeth bright and your gums healthy.</p></div>
</div>

<!-- Welcome -->
<div class="abs welcome">
  <h2>Welcome To <span>The Bright Arch Clinic</span></h2>
  <p>Our team blends gentle care with modern tools to give every patient a calm and easy visit. From routine checkups to full smile makeovers, we plan each step with you and explain every option clearly. We keep our hours flexible, our rooms bright and our prices open, so caring for your smile fits right into a busy life. Come meet us and see the difference a modern practice makes.</p>
  <span class="btn">Read More About Us</span>
</div>
<div class="abs welcome-img ph" role="img" aria-label="Close-up of a patient with a clear aligner"></div>

<!-- Services -->
<div class="abs services">
  <h2 class="sec-title">Struggling with an Oral Issue?<br><span>We Can Help!</span></h2>
  <div class="svc-row">
    <div class="svc"><svg width="56" height="56" viewBox="0 0 56 56" fill="none" stroke="#00a990" stroke-width="2"><path d="M14 10c-6 0-9 6-7 14 2 8 4 22 8 22s4-12 7-12 3 12 7 12 6-14 8-22c2-8-1-14-7-14-4 0-6 2-8 2s-4-2-8-2z"/><path d="M10 24h34"/></svg><h3>Orthodontics</h3><p class="small">Straight teeth with braces made to fit you.</p></div>
    <div class="svc"><svg width="56" height="56" viewBox="0 0 56 56" fill="none" stroke="#00a990" stroke-width="2"><path d="M8 22c0-8 8-12 20-12s20 4 20 12-6 16-20 16S8 30 8 22z"/><path d="M14 22h28M18 18v8M28 16v10M38 18v8"/></svg><h3>Clear Aligners</h3><p class="small">Clear aligners that nobody will notice.</p></div>
    <div class="svc"><svg width="56" height="56" viewBox="0 0 56 56" fill="none" stroke="#00a990" stroke-width="2"><path d="M18 10c-6 0-9 6-7 14 2 8 4 22 8 22s3-12 6-12 3 12 7 12 6-14 8-22c2-8-1-14-7-14-4 0-5 2-7 2s-4-2-8-2z"/><path d="M42 6l2 4 4 2-4 2-2 4-2-4-4-2 4-2z"/></svg><h3>Cosmetic Dentistry</h3><p class="small">Whitening and veneers for a bright smile.</p></div>
    <div class="svc"><svg width="56" height="56" viewBox="0 0 56 56" fill="none" stroke="#00a990" stroke-width="2"><path d="M16 12c-6 0-9 6-7 14 2 8 4 20 8 20s4-10 7-10 3 10 7 10 6-12 8-20c2-8-1-14-7-14-4 0-6 2-8 2s-4-2-8-2z"/><path d="M16 20c1-2 3-3 5-3"/></svg><h3>Pediatric Dentistry</h3><p class="small">Gentle visits made fun for little ones.</p></div>
    <div class="svc"><svg width="56" height="56" viewBox="0 0 56 56" fill="none" stroke="#00a990" stroke-width="2"><path d="M16 8c-6 0-8 4-7 9 1 4 4 6 19 6s18-2 19-6c1-5-1-9-7-9-4 0-6 2-12 2s-8-2-12-2z"/><path d="M24 23v4h8v-4M22 30h12M23 35h10M24 40h8M26 45h4"/></svg><h3>Implant Dentistry</h3><p class="small">Lasting implants that feel like your own.</p></div>
  </div>
  <span class="btn">View All Services</span>
</div>

<!-- Reviews -->
<div class="abs reviews"><h2 class="sec-title">Clients <span>Reviews</span></h2></div>
<div class="abs review">
  <p class="small">The whole team made me feel at ease from the moment I walked in. My cleaning was quick and painless, the staff explained every step, and I left with a smile I am proud to share.</p>
  <div class="quote">”</div>
  <p style="font-size:14px;margin-top:6px">- Client Name</p>
</div>
<div class="abs avatar ph" role="img" aria-label="Client portrait"></div>
<div class="abs dots"><i class="on"></i><i></i><i></i></div>

<!-- Blog -->
<div class="abs blog"><h2 class="sec-title">Blog <span>Posts</span></h2></div>
<div class="abs post-text" style="left:70px;top:2900px">
  <div class="date">10 August 2019</div>
  <h3>Lorem Ipsum Damet</h3>
  <p class="small">Simple steps to help your kids build a great brushing habit at home.</p>
  <a>READ MORE</a>
</div>
<div class="abs post-img ph" role="img" aria-label="Mother and children brushing teeth together" style="left:345px;top:2900px;background:linear-gradient(135deg,#f3e6dc,#d8b9a3)"></div>
<div class="abs post-img ph" role="img" aria-label="Dentist examining a patient" style="left:610px;top:2900px;background:linear-gradient(135deg,#dfe5ea,#8f9ea9)"></div>
<div class="abs post-text" style="left:875px;top:2900px">
  <div class="date">10 August 2019</div>
  <h3>Lorem Ipsum Damet</h3>
  <p class="small">What to expect at a checkup and why regular visits really matter.</p>
  <a>READ MORE</a>
</div>

<!-- Team -->
<div class="abs team ph" role="img" aria-label="Dental team at work, tinted blue">
  <h2>Meet The Team</h2>
  <p>Skilled dentists, hygienists and staff who care about your comfort at every visit.</p>
  <span class="btn">Meet Team</span>
</div>

<!-- Contact -->
<div class="abs contact">
  <h2>Contact <span>Us</span></h2>
  <div class="field">Name</div>
  <div class="field">Email</div>
  <div class="field">Phone</div>
  <div class="field tall">Message / Comments</div>
  <span class="btn">Send Message</span>
</div>
<div class="abs touch">
  <h2>Get In Touch</h2>
  <ul>
    <li><svg width="18" height="18" viewBox="0 0 24 24"><path d="M6.6 10.8a15 15 0 0 0 6.6 6.6l2.2-2.2c.3-.3.7-.4 1-.2 1.1.4 2.3.6 3.6.6.6 0 1 .4 1 1V20c0 .6-.4 1-1 1A17 17 0 0 1 3 4c0-.6.4-1 1-1h3.5c.6 0 1 .4 1 1 0 1.3.2 2.5.6 3.6.1.3 0 .7-.2 1z" fill="#fff"/></svg>617-555-0147</li>
    <li><svg width="18" height="18" viewBox="0 0 24 24" fill="none" stroke="#fff" stroke-width="2"><rect x="3" y="5" width="18" height="14"/><path d="M3 5l9 8 9-8"/></svg>info@brightarchclinic.com</li>
    <li><svg width="18" height="18" viewBox="0 0 24 24" fill="none" stroke="#fff" stroke-width="2"><circle cx="12" cy="12" r="9"/><path d="M12 7v5l3 2"/></svg>Mon-Sat : 8 am To 6 pm<br>Sunday : Closed</li>
    <li><svg width="18" height="18" viewBox="0 0 24 24"><path d="M12 2a7 7 0 0 0-7 7c0 5 7 13 7 13s7-8 7-13a7 7 0 0 0-7-7zm0 9.5A2.5 2.5 0 1 1 12 6.5a2.5 2.5 0 0 1 0 5z" fill="#fff"/></svg>250 Harbor Lane,<br>Suite 12,<br>Milton MA 02186</li>
  </ul>
</div>

<!-- Footer -->
<div class="abs footer">
  <div class="abs fcol" style="left:70px;width:230px">
    <div class="logo" style="position:static"><b></b><span>THE BRIGHT ARCH CLINIC</span></div>
    <p class="small" style="margin-top:16px">Modern, caring dentistry for the whole family, all under one roof.</p>
    <div class="fsocial"><i></i><i></i><i></i><i></i></div>
  </div>
  <div class="abs fcol" style="left:370px"><h4>Our <span>Services</span></h4><ul>
    <li>Orthodontics</li><li>Cleaning &amp; Prevention</li><li>Cosmetic Dentistry</li><li>Implant Dentistry</li><li>Removable Dentures</li><li>Clear Aligners</li><li>Pediatric Dentistry</li><li>Multi Specialty Treatment</li></ul></div>
  <div class="abs fcol" style="left:620px"><h4>Quick <span>Links</span></h4><ul>
    <li>Home</li><li>About Us</li><li>Services</li><li>Patient Info</li><li>Cases &amp; Reviews</li><li>Blog</li><li>Contact</li></ul></div>
  <div class="abs fcol" style="left:885px;width:250px"><h4>Subscribe <span>Newsletter</span></h4>
    <p class="small">Get clinic news, simple tips and offers sent to your inbox.</p>
    <div class="email-box">Enter Email Id</div>
    <span class="btn" style="margin-top:14px;padding:11px 22px">Subscribe</span>
  </div>
</div>
<div class="abs copy">© 2019 The Bright Arch Clinic. All rights reserved.</div>

</body>
</html>
```